Vantor Wear and Fuel is looking for a Clothing/Supplement Online Store Website!

Must be convenient, and user friendly, with vibrant colors that catch the eye!

Target Market(s)

Athletes, and Fashion Customers

Industry/Entity Type

Fitness

Coding

Coded - Design and coding required

Number of Pages Required

3 page

Font styles to use
Decorative

Colors

Designer to choose colors to be used in the design.

Requirements
Must have
• Somewhere to feature products, features to promote discounts and make announcements.
Nice to have
• My logos on each page

```html
<!DOCTYPE html>
<html lang="en">
<head>
<meta charset="utf-8">
<title>Vantor Wear and Fuel</title>
<link href="https://fonts.googleapis.com/css2?family=Russo+One&family=Didact+Gothic&display=swap" rel="stylesheet">
<style>
:root{
  --teal:#23b3b5;
  --teal-dark:#1a9c9e;
  --pink:#f55a75;
  --ink:#222;
  --muted:#666;
  --dark:#2b2b2b;
  --footer:#2a2a2a;
  --light:#f6f6f6;
  --white:#fff;
}
*{box-sizing:border-box;margin:0;padding:0}
html,body{width:1200px;height:5080px;overflow:hidden}
body{position:relative;background:var(--white);font-family:"Didact Gothic",sans-serif;color:var(--ink)}
.abs{position:absolute}
.section-title{position:absolute;left:0;width:1200px;text-align:center;font-family:"Russo One",sans-serif;font-size:32px;letter-spacing:2px;color:var(--teal)}
.section-title .accent{color:var(--pink)}
.btn{position:absolute;display:flex;align-items:center;justify-content:center;gap:8px;height:34px;border-radius:3px;color:#fff;font-size:14px;padding:0 10px;white-space:nowrap}
.btn .dot{width:22px;height:22px;border-radius:50%;background:#fff;display:inline-block;position:relative;flex:none}
.btn .dot::after{content:"";position:absolute;left:6px;top:8px;width:6px;height:6px;border-top:2px solid currentColor;border-right:2px solid currentColor;transform:rotate(45deg)}
.btn-pink{background:var(--pink)}
.btn-pink .dot{color:var(--pink)}
.btn-teal{background:var(--teal)}
.btn-teal .dot{color:var(--teal)}
.photo{position:absolute}

/* header */
.header{position:absolute;left:0;top:0;width:1200px;height:96px;background:#fff}
.logo{position:absolute;left:142px;top:30px;font-family:"Russo One",sans-serif;font-size:30px;color:var(--dark);letter-spacing:2px}
.nav a{position:absolute;top:38px;font-size:15px;color:#333;text-decoration:none}
.nav a.active{color:var(--teal);border-bottom:2px solid var(--teal);padding-bottom:3px}
.search{position:absolute;left:1028px;top:32px;width:34px;height:34px;border-radius:50%;background:var(--teal)}

/* hero */
.hero{position:absolute;left:0;top:96px;width:1200px;height:626px;overflow:hidden;background:var(--dark)}
.hero-title{position:absolute;left:624px;top:430px;font-family:"Russo One",sans-serif;font-size:40px;color:#fff;letter-spacing:1px}
.hero-sub{position:absolute;left:626px;top:484px;font-size:17px;color:#fff}
.hero-arrow{position:absolute;top:585px;width:57px;height:41px;display:flex;align-items:center;justify-content:center}

/* about */
.about-lead{position:absolute;left:142px;top:876px;width:440px;font-size:13.5px;font-weight:bold;line-height:22px;color:#111}
.about-text{position:absolute;left:142px;width:440px;font-size:12px;line-height:20.5px;color:#444}

/* products */
.featured{position:absolute;left:0;top:1376px;width:1200px;height:1200px;background:var(--light)}
.card{position:absolute;width:282px;height:425px;background:#fff;box-shadow:0 3px 14px rgba(0,0,0,.08);overflow:hidden}
.card .top{position:absolute;left:0;top:0;width:282px;height:170px}
.card .plus{position:absolute;left:14px;top:14px;width:18px;height:18px;border:1.5px solid #fff;color:#fff;font-size:14px;line-height:14px;text-align:center}
.card .name{position:absolute;left:0;top:248px;width:100%;text-align:center;font-size:18px;color:#222}
.card .desc{position:absolute;left:30px;top:286px;width:222px;text-align:center;font-size:13px;line-height:21px;color:#555}
.card .btn{left:70px;top:347px;width:142px}
.round-arrow{position:absolute;width:32px;height:32px;border:1px solid #aaa;border-radius:50%;display:flex;align-items:center;justify-content:center;background:#fff}

/* reviews */
.avatar{position:absolute;border-radius:50%;border:4px solid #fff;box-shadow:0 2px 10px rgba(0,0,0,.15)}
.quote{position:absolute;left:270px;top:3034px;width:660px;text-align:center;font-size:13.5px;line-height:22px;color:#444}

/* blog */
.blog-band{position:absolute;left:0;top:3229px;width:1200px;height:297px;background:var(--pink)}
.post{position:absolute;top:3431px;width:284px;height:442px;background:#fff;box-shadow:0 3px 14px rgba(0,0,0,.1);overflow:hidden;text-align:center}
.post .meta{position:absolute;top:244px;width:100%;font-size:13px;color:var(--teal)}
.post .title{position:absolute;top:274px;width:100%;font-size:17px;color:#222}
.post .desc{position:absolute;left:30px;top:310px;width:224px;font-size:13px;line-height:21px;color:#555}
.post .btn{left:82px;top:374px;width:120px}
.chev{position:absolute;top:3590px}

/* deal */
.deal-box{position:absolute;left:259px;top:4211px;width:700px;height:282px;border:1.5px solid var(--teal);background:#fff}

/* newsletter */
.newsletter-input{position:absolute;left:567px;top:4646px;width:341px;height:36px;border:1px solid #e0e0e0;border-radius:18px;font-size:12px;color:#444;padding:10px 18px}
.subscribe{position:absolute;left:920px;top:4646px;width:140px;height:36px;border:1.5px solid var(--teal);border-radius:18px;font-size:14px;text-align:center;line-height:33px;color:#333}

/* footer */
.footer{position:absolute;left:0;top:4728px;width:1200px;height:352px;background:var(--footer);color:#ddd}
.f-head{position:absolute;top:62px;font-size:13px;color:#fff;letter-spacing:.5px}
.f-head::after{content:"";position:absolute;left:0;top:22px;width:30px;height:1px;background:#888}
.f-link{position:absolute;left:157px;font-size:13px;color:#ccc}
.f-link::before{content:"›";position:absolute;left:-14px;color:#888}
.f-link.active{color:var(--pink)}
.f-text{position:absolute;left:340px;font-size:12.5px;line-height:19px;color:#ccc}
.f-icon{position:absolute;left:314px;color:var(--teal);font-size:13px}
.social{position:absolute;top:238px;width:32px;height:32px;border-radius:50%;background:var(--teal)}
.copy{position:absolute;left:0;top:318px;width:1200px;text-align:center;font-size:13px;color:#ccc}
</style>
</head>
<body>

<header class="header">
  <div class="logo">VANTOR</div>
  <nav class="nav">
    <a class="active" style="left:510px">Home</a>
    <a style="left:606px">About Us</a>
    <a style="left:722px">Products</a>
    <a style="left:834px">Blog</a>
    <a style="left:918px">Contact Us</a>
  </nav>
  <div class="search">
    <svg width="34" height="34" viewBox="0 0 34 34"><circle cx="15.5" cy="15.5" r="5" fill="none" stroke="#fff" stroke-width="2"/><line x1="19" y1="19" x2="23" y2="23" stroke="#fff" stroke-width="2"/></svg>
  </div>
</header>

<section class="hero">
  <svg class="abs" style="left:0;top:0" width="1200" height="626">
    <polygon points="661,0 1200,0 1200,626 455,626" fill="var(--teal)"/>
  </svg>
  <div class="photo" role="img" aria-label="Smiling couple embracing" style="left:80px;top:20px;width:500px;height:606px;background:radial-gradient(ellipse at 50% 45%,#d9b39a 0%,#9a7b6a 45%,rgba(43,43,43,0) 75%)"></div>
  <div class="photo" role="img" aria-label="Three white protein supplement tubs" style="left:622px;top:100px;width:444px;height:290px;border-radius:20px;background:linear-gradient(180deg,#f4f4f4,#d8dde0)"></div>
  <div class="hero-title">Nutritional Products</div>
  <div class="hero-sub">What Your Body Needs To Trive</div>
  <div class="btn btn-pink" style="left:624px;top:524px;width:156px;font-size:13px">Visit Our Store <span class="dot"></span></div>
  <div class="hero-arrow" style="left:1086px;background:#cfcfcf">
    <svg width="26" height="12"><path d="M1 6h24M1 6l6-5M1 6l6 5" stroke="#333" stroke-width="1.5" fill="none"/></svg>
  </div>
  <div class="hero-arrow" style="left:1143px;background:var(--pink)">
    <svg width="26" height="12"><path d="M1 6h24M25 6l-6-5M25 6l-6 5" stroke="#fff" stroke-width="1.5" fill="none"/></svg>
  </div>
</section>

<h2 class="section-title" style="top:808px">ABOUT US</h2>
<p class="about-lead">Lorem ipsum dolor sit amet, consectetuer adipiscing elit, sed iamweri nonummy nibh euismod tinciduntut.</p>
<p class="about-text" style="top:934px">Lorem ipsum dolor sit amet, consectetuer adipiscing elit, sed diam nonummy nibh euismod tincidunt ut laoreet dolore magna aliquam erat volutpat. Ut wisi enim ad minim veniam, quis nostrud exerci tation ullamcorper suscipit lobortis nisl ut aliquip ex ea commodo consequat. Duis autem vel eum iriureee dolor in hendrerit in vulputate velit esse molestie consequat, vel illum dolore eu feugiat duis dolore te feugait nulla facilisi.</p>
<p class="about-text" style="top:1071px">Lorem ipsum dolor sit amet, consectetuer adipiscing elit, sed diam nonummy nibh euismod tincidunt ut laoreet dolore magna aliquam erat volutpat. Ut wisi enim ad minim veniam, quis nostrud exerci tation ullamcorper suscipit lobortis nisl ut aliquip ex ea commodo consequat. Duis autem vel eum iriureee dolor in hendrerit in vulputate velit esse molestie consequat</p>
<div class="btn btn-teal" style="left:142px;top:1192px;width:118px;font-size:13px">Read More <span class="dot"></span></div>
<div class="photo" role="img" aria-label="Woman jogging outdoors in a blue hoodie" style="left:736px;top:855px;width:324px;height:324px;border-radius:50%;border:3px solid var(--teal);background:linear-gradient(160deg,#c9d4dc,#5c7a95)"></div>
<div class="photo" role="img" aria-label="Supplement bottle with spilled tablets" style="left:635px;top:1020px;width:198px;height:198px;border-radius:50%;border:3px solid var(--teal);box-shadow:inset 0 0 0 6px #fff;background:linear-gradient(160deg,#f3f3ee,#dfe4c8)"></div>

<section class="featured"></section>
<h2 class="section-title" style="top:1516px">FEATURED <span class="accent">PRODUCTS</span></h2>

<div class="round-arrow" style="left:88px;top:2018px"><svg width="10" height="12"><path d="M7 1L2 6l5 5" stroke="#888" fill="none" stroke-width="1.5"/></svg></div>
<div class="round-arrow" style="left:1086px;top:2018px"><svg width="10" height="12"><path d="M3 1l5 5-5 5" stroke="#888" fill="none" stroke-width="1.5"/></svg></div>

<div class="card" style="left:142px;top:1585px">
  <svg class="top" viewBox="0 0 282 170"><path d="M0 0H282V150Q141 110 0 150Z" fill="var(--teal)"/><path d="M0 150Q141 110 282 150V156Q141 118 0 156Z" fill="var(--pink)"/></svg>
  <div class="plus">+</div>
  <div class="photo" role="img" aria-label="Pink and black supplement tub" style="left:90px;top:40px;width:104px;height:180px;border-radius:12px;background:linear-gradient(180deg,#c23a86,#2a1a24)"></div>
  <div class="name">Product 1</div>
  <div class="desc">Lorem ipsum dolor sit amet wererw consectetuer adipiscing</div>
  <div class="btn btn-teal">View Details <span class="dot"></span></div>
</div>
<div class="card" style="left:462px;top:1585px">
  <svg class="top" viewBox="0 0 282 170"><path d="M0 0H282V150Q141 110 0 150Z" fill="var(--teal)"/><path d="M0 150Q141 110 282 150V156Q141 118 0 156Z" fill="var(--pink)"/></svg>
  <div class="plus">+</div>
  <div class="photo" role="img" aria-label="Dark grey athletic t-shirt" style="left:66px;top:40px;width:150px;height:180px;border-radius:14px;background:linear-gradient(180deg,#5a5d5f,#3c3f41)"></div>
  <div class="name">Product 2</div>
  <div class="desc">Lorem ipsum dolor sit amet wererw consectetuer adipiscing</div>
  <div class="btn btn-pink">View Details <span class="dot"></span></div>
</div>
<div class="card" style="left:780px;top:1585px">
  <svg class="top" viewBox="0 0 282 170"><path d="M0 0H282V150Q141 110 0 150Z" fill="var(--teal)"/><path d="M0 150Q141 110 282 150V156Q141 118 0 156Z" fill="var(--pink)"/></svg>
  <div class="plus">+</div>
  <div class="photo" role="img" aria-label="Blue creatine supplement tub" style="left:82px;top:40px;width:118px;height:180px;border-radius:10px;background:linear-gradient(180deg,#2e3fa8,#141a55)"></div>
  <div class="name">Product 3</div>
  <div class="desc">Lorem ipsum dolor sit amet wererw consectetuer adipiscing</div>
  <div class="btn btn-teal">View Details <span class="dot"></span></div>
</div>
<div class="card" style="left:142px;top:2059px">
  <svg class="top" viewBox="0 0 282 170"><path d="M0 0H282V150Q141 110 0 150Z" fill="var(--teal)"/><path d="M0 150Q141 110 282 150V156Q141 118 0 156Z" fill="var(--pink)"/></svg>
  <div class="plus">+</div>
  <div class="photo" role="img" aria-label="Pink and black supplement tub" style="left:90px;top:40px;width:104px;height:180px;border-radius:12px;background:linear-gradient(180deg,#c23a86,#2a1a24)"></div>
  <div class="name">Product 4</div>
  <div class="desc">Lorem ipsum dolor sit amet wererw consectetuer adipiscing</div>
  <div class="btn btn-teal">View Details <span class="dot"></span></div>
</div>
<div class="card" style="left:462px;top:2059px">
  <svg class="top" viewBox="0 0 282 170"><path d="M0 0H282V150Q141 110 0 150Z" fill="var(--teal)"/><path d="M0 150Q141 110 282 150V156Q141 118 0 156Z" fill="var(--pink)"/></svg>
  <div class="plus">+</div>
  <div class="photo" role="img" aria-label="Dark grey athletic t-shirt" style="left:66px;top:40px;width:150px;height:180px;border-radius:14px;background:linear-gradient(180deg,#5a5d5f,#3c3f41)"></div>
  <div class="name">Product 5</div>
  <div class="desc">Lorem ipsum dolor sit amet wererw consectetuer adipiscing</div>
  <div class="btn btn-teal">View Details <span class="dot"></span></div>
</div>
<div class="card" style="left:780px;top:2059px">
  <svg class="top" viewBox="0 0 282 170"><path d="M0 0H282V150Q141 110 0 150Z" fill="var(--teal)"/><path d="M0 150Q141 110 282 150V156Q141 118 0 156Z" fill="var(--pink)"/></svg>
  <div class="plus">+</div>
  <div class="photo" role="img" aria-label="Blue creatine supplement tub" style="left:82px;top:40px;width:118px;height:180px;border-radius:10px;background:linear-gradient(180deg,#2e3fa8,#141a55)"></div>
  <div class="name">Product 6</div>
  <div class="desc">Lorem ipsum dolor sit amet wererw consectetuer adipiscing</div>
  <div class="btn btn-teal">View Details <span class="dot"></span></div>
</div>

<h2 class="section-title" style="top:2702px">CUSTOMER <span class="accent">REVIEWS</span></h2>
<div class="avatar" role="img" aria-label="Customer portrait" style="left:296px;top:2781px;width:142px;height:142px;background:linear-gradient(160deg,#c9a58a,#6d4e3e)"></div>
<div class="avatar" role="img" aria-label="Customer portrait" style="left:511px;top:2763px;width:178px;height:178px;background:linear-gradient(160deg,#e2c1a6,#8a6a55)"></div>
<div class="avatar" role="img" aria-label="Customer portrait" style="left:762px;top:2781px;width:142px;height:142px;background:linear-gradient(160deg,#e3c0a5,#7a5442)"></div>
<div class="abs" style="left:0;top:2968px;width:1200px;text-align:center;font-size:15px;color:var(--teal)">Lorem ipsum dolor</div>
<div class="abs" style="left:0;top:2999px;width:1200px;text-align:center;font-size:13px;color:#f0a020;letter-spacing:2px">★★★★★</div>
<div class="abs" style="left:272px;top:3018px;font-family:Georgia,serif;font-size:56px;color:#ddd;line-height:1">“</div>
<div class="abs" style="left:790px;top:3070px;font-family:Georgia,serif;font-size:56px;color:#ddd;line-height:1">”</div>
<p class="quote">Lorem ipsum dolor sit amet, consectetuer adipiscing elit, sed diam nonummy nibh euismod laoreet dolore magna aliquam erat volutpat. et accumsan et iusto odio dignissim qui blandit praesent luptatum zzril delenit augue duis dolore te feugait nulla facilisi.</p>
<div class="abs" style="left:0;top:3130px;width:1200px;text-align:center;font-size:14px;color:#444">- Dario Kemp</div>
<div class="round-arrow" style="left:200px;top:3042px;width:30px;height:30px"><svg width="10" height="12"><path d="M7 1L2 6l5 5" stroke="#888" fill="none" stroke-width="1.5"/></svg></div>
<div class="round-arrow" style="left:966px;top:3042px;width:30px;height:30px"><svg width="10" height="12"><path d="M3 1l5 5-5 5" stroke="#888" fill="none" stroke-width="1.5"/></svg></div>

<div class="blog-band"></div>
<h2 class="section-title" style="top:3364px;color:#fff">LATEST BLOG POSTS</h2>
<svg class="chev" style="left:86px" width="24" height="66"><path d="M20 2L4 33l16 31" stroke="#bbb" stroke-width="2" fill="none"/></svg>
<svg class="chev" style="left:1090px" width="24" height="66"><path d="M4 2l16 31L4 64" stroke="#bbb" stroke-width="2" fill="none"/></svg>

<article class="post" style="left:140px">
  <div class="photo" role="img" aria-label="Fit man and woman posing in athletic wear" style="left:0;top:0;width:284px;height:194px;background:linear-gradient(180deg,#eef0f1,#cdb7a4)"></div>
  <div class="abs" style="left:116px;top:164px;width:52px;height:52px;border-radius:50%;background:#fff"></div>
  <div class="meta">22 Oct 2019 / By Admin</div>
  <div class="title">Lorem ipsum dolor amet</div>
  <div class="desc">Lorem ipsum dolor sita consecte adipiscing elit, sed diam</div>
  <div class="btn btn-teal">Read More <span class="dot"></span></div>
</article>
<article class="post" style="left:458px">
  <div class="photo" role="img" aria-label="Indoor cycling class" style="left:0;top:0;width:284px;height:194px;background:linear-gradient(180deg,#2c3e66,#18233d)"></div>
  <div class="abs" style="left:116px;top:164px;width:52px;height:52px;border-radius:50%;background:#fff"></div>
  <div class="meta">20 Oct 2019 / By Admin</div>
  <div class="title">Lorem ipsum dolor amet</div>
  <div class="desc">Lorem ipsum dolor sita consecte adipiscing elit, sed diam</div>
  <div class="btn btn-teal">Read More <span class="dot"></span></div>
</article>
<article class="post" style="left:778px">
  <div class="photo" role="img" aria-label="Dumbbells on a gym rack" style="left:0;top:0;width:284px;height:194px;background:linear-gradient(180deg,#b8b8b8,#4e4e4e)"></div>
  <div class="abs" style="left:116px;top:164px;width:52px;height:52px;border-radius:50%;background:#fff"></div>
  <div class="meta">18 Oct 2019 / By Admin</div>
  <div class="title">Lorem ipsum dolor amet</div>
  <div class="desc">Lorem ipsum dolor sita consecte adipiscing elit, sed diam</div>
  <div class="btn btn-teal">Read More <span class="dot"></span></div>
</article>
<div class="btn btn-pink" style="left:537px;top:3931px;width:126px;font-size:13px">View More <span class="dot"></span></div>

<h2 class="section-title" style="top:4101px">DEAL OF <span class="accent">THE WEEK</span></h2>
<div class="deal-box"></div>
<div class="photo" role="img" aria-label="Excited couple giving thumbs up" style="left:237px;top:4155px;width:256px;height:338px;background:linear-gradient(180deg,#d8b89e 0%,#f1f1f1 55%,#e6e6e6 100%);border-radius:40% 40% 0 0"></div>
<div class="photo" role="img" aria-label="Two white supplement bottles" style="left:483px;top:4273px;width:178px;height:178px;border-radius:50%;background:var(--teal);border:3px solid #fff;box-shadow:0 0 0 1px var(--teal)"></div>
<div class="abs" style="left:600px;top:4266px;width:46px;height:46px;border-radius:50%;background:var(--pink);color:#fff;font-size:13px;text-align:center;line-height:46px">-50%</div>
<div class="abs" style="left:681px;top:4288px;font-size:22px;color:#222">Product 1</div>
<div class="abs" style="left:681px;top:4324px;font-size:20px;color:#888;white-space:nowrap"><s>$37.94</s> <span style="color:var(--pink)">– $18.97</span> <span style="font-size:12px;color:var(--pink);margin-left:6px">You save 50%</span></div>
<div class="abs" style="left:681px;top:4360px;font-size:12px;color:#555">Deal ends in : &nbsp;◷ <b>37</b> h. &nbsp;<b>55</b> m. &nbsp;<b>59</b> s.</div>
<div class="btn btn-pink" style="left:681px;top:4400px;width:156px;font-size:13px">Visit Our Store <span class="dot"></span></div>

<svg class="abs" style="left:138px;top:4646px" width="50" height="36"><rect x="1" y="1" width="48" height="34" fill="none" stroke="var(--teal)" stroke-width="2"/><path d="M1 1l24 20L49 1M1 35l18-16M49 35L31 19" fill="none" stroke="var(--teal)" stroke-width="2"/></svg>
<div class="abs" style="left:204px;top:4634px;font-size:17px;color:#222">Newsletter Sign Up</div>
<div class="abs" style="left:204px;top:4660px;font-size:11.5px;color:#555">Subscribe Now And Receive Weekly Newsletter From Us!</div>
<div class="newsletter-input">Enter Email Here</div>
<div class="subscribe">SUBSCRIBE</div>

<footer class="footer">
  <div class="f-head" style="left:142px">QUICK LINKS</div>
  <div class="f-head" style="left:314px">CONTACT DETAILS</div>
  <div class="f-head" style="left:567px">LOCATION MAP</div>

  <div class="f-link active" style="top:108px">Home</div>
  <div class="f-link" style="top:141px">About Us</div>
  <div class="f-link" style="top:175px">Products</div>
  <div class="f-link" style="top:210px">Blog</div>
  <div class="f-link" style="top:244px">Contact Us</div>

  <div class="f-icon" style="top:108px">
    <svg width="12" height="16"><path d="M6 15C2 9 1 7 1 5.5a5 5 0 0110 0C11 7 10 9 6 15z" fill="var(--teal)"/><circle cx="6" cy="5.5" r="2" fill="var(--footer)"/></svg>
  </div>
  <div class="f-text" style="top:106px;color:#fff">VANTOR</div>
  <div class="f-text" style="top:133px">123 Building Name, Area<br>Name, Street, City,<br>Country - Zipcode</div>
  <div class="f-icon" style="top:210px">
    <svg width="14" height="14"><path d="M3 1l3 3-2 2c1 2 2 3 4 4l2-2 3 3-2 2C6 13 1 8 1 3z" fill="var(--teal)"/></svg>
  </div>
  <div class="f-text" style="top:208px">123 456 7890</div>
  <div class="f-icon" style="top:252px">
    <svg width="14" height="11"><rect x="0.5" y="0.5" width="13" height="10" fill="var(--teal)"/><path d="M1 1l6 5 6-5" stroke="var(--footer)" fill="none"/></svg>
  </div>
  <div class="f-text" style="top:249px">info@vantorfuel.com</div>

  <div class="photo" role="img" aria-label="Street map showing store location" style="left:567px;top:111px;width:217px;height:159px;background:linear-gradient(135deg,#eef0ec,#d6dfe2)"></div>

  <div class="abs" style="left:853px;top:158px;width:209px;text-align:center;font-family:'Russo One',sans-serif;font-size:32px;color:#fff;letter-spacing:2px">VANTOR</div>
  <div class="social" style="left:896px"></div>
  <div class="social" style="left:941px"></div>
  <div class="social" style="left:987px"></div>

  <div class="abs" style="left:142px;top:298px;width:920px;height:1px;background:#555"></div>
  <div class="copy">Copyright © 2019 Vantor. All Right Reserved.</div>
</footer>

</body>
</html>
```